Young, dynamic furniture company needs a new business card design

We require a new business card design for our modern furniture company which supplies furniture and appliances to the property and development market.
Oakridge Interiors has become one of the leading furniture & appliance suppliers to the property market withing London. With over 10 years experience, we have increased our business to supply not only private landlords and managing agents, but also property developers, housing associations and local councils.
We offer not only a complete range of furniture which includes beds, wardrobes, dining sets and sofas, but also a high quality, full delivery and assembly service to help you with all our furnishing needs.

Target Market(s)

Private landlords, estate agents, letting agents, property management companies

Industry/Entity Type

Business

Contact Information for Business Card

Name,
Title,
Address,
Mobile,
Telephone,
Fax, Website, email address

Font styles to use
Sans Serif

Colors
3176b5
0555a3
85abd2
cfdeed

Requirements
Must have
• All the above information for each of our staff, along with our logo

```html
<!DOCTYPE html>
<html lang="en">
<head>
<meta charset="utf-8">
<title>Oakridge Interiors — Business Card</title>
<link rel="stylesheet" href="https://fonts.googleapis.com/css2?family=Roboto+Condensed:wght@300;400;700&display=swap">
<style>
  :root {
    --brand-blue: #3176b5;
    --brand-deep: #0555a3;
    --brand-navy: #1f3f86;
    --brand-light: #85abd2;
    --brand-pale: #cfdeed;
    --ink: #4a4f57;
    --ink-soft: #6b717a;
    --paper: #ffffff;
    --backdrop: #e6e8eb;
  }
  * { box-sizing: border-box; margin: 0; padding: 0; }
  html, body {
    width: 1200px; height: 950px; overflow: hidden;
    background: var(--backdrop);
    font-family: "Roboto Condensed", Arial, sans-serif;
  }
  .sheet {
    width: 1200px; height: 950px;
    display: flex; flex-direction: column; align-items: center; justify-content: center;
    gap: 50px;
  }
  .card {
    position: relative;
    width: 700px; height: 400px;
    overflow: hidden;
    box-shadow: 0 6px 18px rgba(0,0,0,.18);
  }

  /* Front */
  .card--front {
    background: var(--brand-blue);
    color: var(--paper);
    display: flex; flex-direction: column; align-items: center; justify-content: center;
    text-align: center;
  }
  .front-brand__name {
    font-weight: 700; font-size: 40px; letter-spacing: 1px; text-transform: uppercase;
  }
  .front-brand__tagline {
    margin-top: 6px; font-weight: 300; font-size: 15px; letter-spacing: 2px; text-transform: uppercase;
  }
  .front-website {
    margin-top: 46px; font-weight: 400; font-size: 17px; letter-spacing: 5px;
  }

  /* Back */
  .card--back { background: var(--paper); }
  .back-shapes { position: absolute; inset: 0; }
  .back-brand {
    position: absolute; top: 46px; right: 48px;
    display: flex; align-items: center; gap: 12px;
  }
  .back-brand__mark { width: 26px; height: 26px; background: var(--brand-deep); }
  .back-brand__text { text-align: right; }
  .back-brand__name {
    color: var(--brand-navy); font-weight: 700; font-size: 28px; text-transform: uppercase; letter-spacing: .5px;
  }
  .back-brand__tagline {
    color: var(--brand-navy); font-weight: 400; font-size: 11px; letter-spacing: 1.5px; text-transform: uppercase; margin-top: 2px;
  }
  .contact-list {
    position: absolute; top: 172px; right: 40px;
    list-style: none; text-align: right;
    color: var(--ink); font-size: 17px; line-height: 25px;
  }
  .contact-list li { display: flex; align-items: center; justify-content: flex-end; gap: 9px; }
  .contact-list svg { width: 15px; height: 15px; fill: var(--brand-navy); flex: none; }
  .person {
    position: absolute; left: 36px; top: 238px; color: var(--paper);
  }
  .person__name { font-weight: 700; font-size: 23px; letter-spacing: 1px; text-transform: uppercase; }
  .person__title { font-weight: 400; font-size: 15px; letter-spacing: 1px; text-transform: uppercase; margin-top: 2px; }
  .address {
    position: absolute; left: 36px; top: 308px;
    font-style: normal; color: var(--ink-soft); font-size: 17px; line-height: 23px;
  }
  .address__web { letter-spacing: 3px; }
</style>
</head>
<body>
<main class="sheet">

  <section class="card card--front" aria-label="Card front">
    <div class="front-brand">
      <div class="front-brand__name">Oakridge Interiors</div>
      <div class="front-brand__tagline">Trade Furniture Solutions</div>
    </div>
    <div class="front-website">www.oakridgeint.co</div>
  </section>

  <section class="card card--back" aria-label="Card back">
    <svg class="back-shapes" viewBox="0 0 700 400" width="700" height="400" aria-hidden="true">
      <line x1="262" y1="151" x2="700" y2="151" stroke="var(--brand-blue)" stroke-width="3"/>
      <polygon points="258,150 268,150 243,226 233,226" fill="var(--brand-blue)"/>
      <polygon points="0,226 238,226 216,296 0,296" fill="var(--brand-navy)"/>
    </svg>

    <div class="back-brand">
      <div class="back-brand__text">
        <div class="back-brand__name">Oakridge Interiors</div>
        <div class="back-brand__tagline">Trade Furniture Solutions</div>
      </div>
      <div class="back-brand__mark"></div>
    </div>

    <ul class="contact-list">
      <li>555 0142 7781
        <svg viewBox="0 0 16 16"><path d="M3 1h3l1.5 4-2 1.2a9 9 0 0 0 4.3 4.3L11 8.5l4 1.5v3c0 1-1 2-2 2A13 13 0 0 1 1 3c0-1 1-2 2-2z"/></svg>
      </li>
      <li>555 0198 3264
        <svg viewBox="0 0 16 16"><path d="M4 0h8a1 1 0 0 1 1 1v14a1 1 0 0 1-1 1H4a1 1 0 0 1-1-1V1a1 1 0 0 1 1-1zm1 2v10h6V2zm3 11a1 1 0 1 0 0 2 1 1 0 0 0 0-2z"/></svg>
      </li>
      <li>555 0163 4907
        <svg viewBox="0 0 16 16"><path d="M4 0h8v5H4zM1 6h14a1 1 0 0 1 1 1v6a1 1 0 0 1-1 1h-2v2H3v-2H1a1 1 0 0 1-1-1V7a1 1 0 0 1 1-1zm4 6v2h6v-2z"/></svg>
      </li>
      <li>mark@oakridgeint.co
        <svg viewBox="0 0 16 16"><path d="M0 3h16v1L8 9 0 4zm0 3 8 5 8-5v7H0z"/></svg>
      </li>
    </ul>

    <div class="person">
      <div class="person__name">Mark Ellison</div>
      <div class="person__title">President</div>
    </div>

    <address class="address">
      27 Linden Grove Road<br>
      Hartwell, NY 10488<br>
      <span class="address__web">www.oakridgeint.co</span>
    </address>
  </section>

</main>
</body>
</html>
```